Real Estate stationery - need an interesting, eye catching design

I need a letterhead and #10 envelope design in the same theme.
I am looking for an interesting, eye catching design that would stand out in the crowd. I am in the real estate business(which is very competitive) in Florida so standing out and being different is very important to me.
Marguerite(Rita) Delacourt (name), RealtorĀ® (title), 352-608-2147 (cell), bayviewritahomes@quellmail.com (email), www.bayviewritahomes.com(website), 915 Calloway Creek Blvd.,Ste. 3140, Longwood, FL 32779 (business address)

```html
<!DOCTYPE html>
<html lang="en">
<head>
<meta charset="utf-8">
<title>Keystone Crest Real Estate Stationery</title>
<link href="https://fonts.googleapis.com/css2?family=Open+Sans:wght@400;600;700&display=swap" rel="stylesheet">
<style>
  :root {
    --bg: #cccccc;
    --paper: #fafafa;
    --brown: #8a6128;
    --ink: #5a5a5a;
    --dark: #3c3c3c;
    --ghost: #ebebeb;
  }
  * { margin: 0; padding: 0; box-sizing: border-box; }
  html, body { width: 1200px; height: 771px; overflow: hidden; background: var(--bg); font-family: "Open Sans", sans-serif; }
  .canvas { position: relative; width: 1200px; height: 771px; }

  .ghost-decor { position: absolute; background: radial-gradient(ellipse at 60% 45%, var(--ghost) 0%, rgba(235,235,235,0.6) 45%, rgba(250,250,250,0) 75%); }

  .brand { color: var(--brown); font-weight: 700; }
  .brand-name { line-height: 1; white-space: nowrap; }
  .brand-sub { white-space: nowrap; }
  .brand-mark { display: inline-block; width: 9px; height: 9px; background: var(--brown); }

  /* Letterhead */
  .letterhead { position: absolute; left: 115px; top: 80px; width: 432px; height: 610px; background: var(--paper); overflow: hidden; }
  .letterhead .ghost-decor { left: 33px; top: 344px; width: 399px; height: 220px; }
  .letterhead .brand { position: absolute; left: 0; right: 0; top: 52px; text-align: center; }
  .letterhead .brand-mark { margin-bottom: 6px; }
  .letterhead .brand-name { font-size: 19px; }
  .letterhead .brand-sub { font-size: 6.5px; letter-spacing: 5px; margin-top: 6px; }

  .letter-body { position: absolute; left: 49px; top: 143px; width: 348px; font-size: 6.2px; line-height: 11px; color: var(--ink); }
  .letter-body .salutation { margin-bottom: 22px; }
  .letter-body p { margin-bottom: 11px; text-align: justify; }

  .sign-off { position: absolute; left: 49px; top: 406px; font-size: 6.5px; color: var(--ink); }
  .sign-name { font-weight: 700; color: var(--dark); }
  .signature { width: 88px; height: 16px; margin: 10px 0 4px -12px; background: linear-gradient(90deg, rgba(74,115,168,0.08), rgba(74,115,168,0.25), rgba(74,115,168,0.06)); border-radius: 8px; }

  .contact { position: absolute; left: 22px; top: 575px; font-size: 6.4px; line-height: 10px; color: var(--dark); }
  .contact-line { display: flex; align-items: center; gap: 4px; }
  .contact svg { width: 7px; height: 7px; fill: var(--brown); }

  .footer-bar { position: absolute; left: 0; bottom: 0; width: 100%; height: 6px; background: var(--dark); }
  .footer-tab { position: absolute; right: 0; bottom: 0; width: 163px; height: 21px; }
  .footer-tab svg { position: absolute; inset: 0; width: 100%; height: 100%; }
  .footer-url { position: absolute; left: 302px; bottom: 6px; font-size: 6.8px; line-height: 10px; color: #fff; }

  /* Envelopes */
  .envelope { position: absolute; left: 588px; width: 496px; height: 208px; background: var(--paper); overflow: hidden; }
  .envelope-front { top: 170px; }
  .envelope-front .ghost-decor { left: 116px; top: 14px; width: 380px; height: 194px; }
  .envelope-front .brand { position: absolute; left: 22px; top: 28px; text-align: left; }
  .envelope-front .brand-name { font-size: 14px; }
  .envelope-front .brand-sub { font-size: 5.5px; letter-spacing: 4px; margin-top: 5px; }
  .return-address { position: absolute; left: 22px; top: 164px; font-size: 6.4px; line-height: 10px; color: var(--dark); }

  .envelope-back { top: 392px; height: 209px; }
  .flap { position: absolute; left: 0; top: 0; width: 496px; height: 64px; }
  .envelope-back .brand { position: absolute; left: 0; right: 0; top: 20px; text-align: center; color: #fff; }
  .envelope-back .brand-name { font-size: 11px; }
  .envelope-back .brand-sub { font-size: 4.5px; letter-spacing: 3px; margin-top: 4px; }
</style>
</head>
<body>
<div class="canvas">

  <section class="letterhead">
    <div class="ghost-decor" role="img" aria-label="Faint background decoration"></div>
    <div class="brand">
      <div class="brand-mark"></div>
      <div class="brand-name">Keystone Crest</div>
      <div class="brand-sub">REAL ESTATE</div>
    </div>

    <div class="letter-body">
      <div class="salutation">Dear Sir,</div>
      <p>Lorem Ipsum is simply dummy text of the printing and typesetting industry. Lorem Ipsum has been the industry's standard dummy text ever since the 1500s, when an unknown printer took a galley of type and scrambled it to make a type specimen book. It has survived not only five centuries, but also the leap into electronic typesetting, remaining essentially unchanged. It was popularised in the 1960s with the release of Veltrane sheets containing Lorem Ipsum passages, and more recently with desktop publishing software like Orvel PageSmith including versions of Lorem Ipsum.</p>
      <p>Lorem Ipsum is simply dummy text of the printing and typesetting industry. Lorem Ipsum has been the industry's standard dummy text ever since the 1500s, when an unknown printer took a galley of type and scrambled it to make a type specimen book. It has survived not only five centuries, but also the leap into electronic typesetting, remaining essentially unchanged. It was popularised in the 1960s with the release of Veltrane sheets containing Lorem Ipsum passages, and more recently with desktop publishing software like Orvel PageSmith including versions of Lorem Ipsum.</p>
      <p>Lorem Ipsum is simply dummy text of the printing and typesetting industry. Lorem Ipsum has been the industry's standard dummy text ever since the 1500s, when an unknown printer took a galley of type and scrambled it to make a type specimen book.</p>
    </div>

    <div class="sign-off">
      <div class="sign-name">Your Name</div>
      <div class="signature" role="img" aria-label="Handwritten signature"></div>
      <div class="sign-title">CEO &nbsp;|&nbsp; Owner</div>
    </div>

    <div class="contact">
      <div class="contact-line">
        <svg viewBox="0 0 10 10"><path d="M1 2.5C1 1.5 2 1 5 1s4 .5 4 1.5V4H7V3H3v1H1z M2 5h6l1 4H1z"/></svg>
        <span>352-608-2147</span>
        <svg viewBox="0 0 10 10"><path d="M1 2h8v6H1z"/></svg>
        <span>bayviewritahomes@quellmail.com</span>
      </div>
      <div class="contact-line">
        <svg viewBox="0 0 10 10"><path d="M5 0a3.5 3.5 0 0 1 3.5 3.5C8.5 6 5 10 5 10S1.5 6 1.5 3.5A3.5 3.5 0 0 1 5 0zm0 2a1.5 1.5 0 1 0 0 3 1.5 1.5 0 0 0 0-3z"/></svg>
        <span>915 Calloway Creek Blvd.,Ste. 3140, Harrow Glen, FL 34619</span>
      </div>
    </div>

    <div class="footer-bar"></div>
    <div class="footer-tab">
      <svg viewBox="0 0 163 21" preserveAspectRatio="none"><path d="M0 21 C10 21 14 0 28 0 H163 V21 Z" fill="#8a6128"/></svg>
    </div>
    <div class="footer-url">www.bayviewritahomes.com</div>
  </section>

  <section class="envelope envelope-front">
    <div class="ghost-decor" role="img" aria-label="Faint background decoration"></div>
    <div class="brand">
      <div class="brand-name">Keystone Crest</div>
      <div class="brand-sub">REAL ESTATE</div>
    </div>
    <div class="return-address">
      915 Calloway Creek Blvd.,<br>Ste. 3140, Harrow Glen, FL 34619
    </div>
  </section>

  <section class="envelope envelope-back">
    <svg class="flap" viewBox="0 0 496 64"><path d="M0 0 H496 L484 42 Q478 64 452 64 H44 Q18 64 12 42 Z" fill="#8a6128"/></svg>
    <div class="brand">
      <div class="brand-name">Keystone Crest</div>
      <div class="brand-sub">REAL ESTATE</div>
    </div>
  </section>

</div>
</body>
</html>
```